The Brighter Living Hour with Dan Kessop.

I'm launching this podcast on health and wellness and I want to be take serious. That starts with a great design. There's too much contradiction out there about what is and isn't healthy. I want my podcast to be a resource that people can rely upon. I want my face in it and I want it to pop with colors that catch the eye. I want It clean and crisp. I was also thinking of experimenting with an animated photo of me as well. What ever looks best.

Industry/Entity Type

Health And Wellness

Font styles to use
Sans Serif

Requirements
Must have
• My face and or body.

```html
<!DOCTYPE html>
<html lang="en">
<head>
<meta charset="utf-8">
<title>The Brighter Living Hour with Dan Kessop</title>
<link rel="stylesheet" href="https://fonts.googleapis.com/css2?family=Anton&display=swap">
<style>
  :root {
    --teal-light: #3a8f98;
    --teal-mid: #1f5f78;
    --navy-deep: #06122a;
    --skin-light: #d29a88;
    --skin-mid: #b86d5f;
    --skin-dark: #8d4a42;
    --title-white: #ffffff;
    --accent-peach: #ebc6b8;
  }
  html, body {
    margin: 0;
    padding: 0;
    width: 1200px;
    height: 1200px;
    overflow: hidden;
    background: var(--navy-deep);
  }
  .cover {
    display: block;
    width: 1200px;
    height: 1200px;
  }
  .title-text {
    font-family: "Anton", "Oswald", sans-serif;
    fill: var(--title-white);
    text-transform: uppercase;
  }
  .title-kicker {
    fill: var(--accent-peach);
    letter-spacing: 6px;
  }
  .title-rule {
    fill: var(--accent-peach);
  }
</style>
</head>
<body>
<svg class="cover" viewBox="0 0 1200 1200" xmlns="http://www.w3.org/2000/svg">
  <defs>
    <linearGradient id="backdrop-gradient" x1="0" y1="0" x2="1" y2="1">
      <stop offset="0" stop-color="var(--teal-light)"/>
      <stop offset="0.5" stop-color="var(--teal-mid)"/>
      <stop offset="1" stop-color="var(--navy-deep)"/>
    </linearGradient>
    <linearGradient id="host-gradient" x1="0" y1="0" x2="1" y2="1">
      <stop offset="0" stop-color="var(--skin-light)"/>
      <stop offset="0.55" stop-color="var(--skin-mid)"/>
      <stop offset="1" stop-color="var(--skin-dark)"/>
    </linearGradient>
  </defs>

  <rect class="backdrop" width="1200" height="1200" fill="url(#backdrop-gradient)"/>

  <path class="host-photo" role="img" aria-label="Photo of host Dan Kessop, shirtless, shown from head to shoulder"
        d="M0 0 H230 C250 120 240 300 200 420 C190 500 220 560 320 590 C470 640 620 700 690 800 C740 880 760 1000 760 1200 H0 Z"
        fill="url(#host-gradient)"/>

  <g class="show-title">
    <text class="title-text title-kicker" x="362" y="400" font-size="60">The</text>
    <text class="title-text title-brighter" x="360" y="580"
          font-size="180" textLength="700" lengthAdjust="spacingAndGlyphs">Brighter</text>
    <text class="title-text title-living" x="360" y="770"
          font-size="190" textLength="700" lengthAdjust="spacingAndGlyphs">Living</text>
    <rect class="title-rule" x="362" y="800" width="140" height="10"/>
    <text class="title-text title-hour" x="360" y="892"
          font-size="64" textLength="150" lengthAdjust="spacingAndGlyphs">Hour</text>
    <text class="title-text title-host" x="540" y="892"
          font-size="64" textLength="520" lengthAdjust="spacingAndGlyphs">with Dan Kessop</text>
  </g>
</svg>
</body>
</html>
```